Church Website with Home Page and Member Sermon Library

I am in need of an updated design for our church website. This will include 4 pages (outlined below). We are a conservative, evangelical, Christian church. The site should be modern and clean, while still reflecting our conservative values. I already have a logo for our church, and I want the site to incorporate the logo, and match the logo/branding. Stock photos are allowed if needed, but I have uploaded some images of our church and would prefer those images to be used if possible. Any stock photos used should not include any people in the photos (scenery, nature, buildings, animals, etc. are fine).

The site will need 4 pages: Home, Support Us (Donate), Login, and Recording Library.

Page 1: Home
The home page should include the following sections:

- Navigation: Should include links to each section of the home page plus a "listen live" link which will take the user to a live-streaming site and a "support us" link which will take the user to a support/donate page.

- Announcements: Can be either a banner or some other design, but there needs to be some way for us to post announcements for visitors to see. I'm open for creative ideas in this section, but would like it not to take up a lot of room on the page.

- About Us: Should include address, service times (see attached document), and information about the church.

- Pastor Bio: A section that introduces our pastor and gives a short bio about our pastor. Would like this section to include a picture of our pastor. Somewhere in this section I would like to include this Bible reference: "And I will give you pastors according to mine heart, which shall feed you with knowledge and understanding. Jer 3:15 LPW"

- Articles of Faith (What We Believe): This should include several sub-sections each with a heading, body, and possibly 1 or more scripture references. I have attached a document to the brief that includes our articles of faith. Feel free to be creative with this section in how you lay these out and format them.

- Support Us: A small section that explains what kind of support someone can give and a link to a donation page. The link can say something like "Support Us" or "Donate Now".

- Contact form: A contact form that allows the visitor to send us a message. The contact form should ask for name, email, phone, and message.

- Footer: A footer that will be displayed on all pages of the site. This should include at a minimum a link to the home page (or a link to each individual section in the home page if you prefer), a link to "listen live", a link to "support us", a link to "contact us" (or you can put the contact form directly in the footer if you prefer), the address, and a "member login" link.

Page 2: Support Us
The donation page should include a form the visitor can fill out to make a donation. We will embed a third party form later. For this design, please just mock out the design with a basic form asking for name, phone, and email.

Page 3: Login
The recording library (detailed below) will require members to login with a shared numeric code before accessing the page. We need a design for a login screen. The screen should include navigation/footer just like all other pages, but the body of the login page will consist only of a form that asks the user to enter the access code and then a "login" button.

Page 4: Recording Library

The library page is a member-only page that will require a shared, numeric pass code to access. On this page, members will be able to access a filterable list of past sermons. The page by default should display most recent sermons, but should also include a search form that allows the member to filter the sermon list to find a particular sermon. The search form should allow the user to select a filter type (e.g. Speaker name, date, event, etc.) and type in a value to search. They should be able to add multiple filters and remove filters that have been added. Each sermon that is displayed in the result list should include basic information such as title, date, speaker, tags, etc. along with a download icon, and an embedded audio player where they can click a play button to stream it on-demand. Each sermon should also have clickable tags associated with it that can be used to find related sermons.
Updates

I have uploaded several images of our church. Feel free to incorporate these into your design if possible.

Target Market(s)

Church Members

Industry/Entity Type

Religion

Number of Pages Required

4 page

Font styles to use
Sans Serif

Colors

Designer to choose colors to be used in the design.

Requirements
Must have
• Must incorporate the logo (attached)
Nice to have
• Would like the design to incorporate pictures of our church (attached) instead of stock photos if possible.
Should not have
• Please avoid an overly cluttered design. Stock photos used should not include any people in the photos.

```html
<!DOCTYPE html>
<html lang="en">
<head>
<meta charset="utf-8">
<title>Cedar Hill Holiness Church</title>
<link href="https://fonts.googleapis.com/css2?family=Josefin+Sans:wght@400;600;700&family=Playfair+Display:wght@600;700&family=Poppins:wght@400;500;600&display=swap" rel="stylesheet">
<style>
:root{
  --green:#4b7b2f;
  --green-dark:#3c6625;
  --green-light:#7fae4e;
  --teal:#1bb4d5;
  --teal-dark:#0e9bbb;
  --sky:#edf8fc;
  --ink:#232323;
  --muted:#6b6b6b;
  --line:#e3e3e3;
  --white:#ffffff;
}
*{box-sizing:border-box;margin:0;padding:0}
html,body{width:1200px;height:5224px;overflow:hidden}
body{position:relative;background:var(--white);font-family:'Poppins',sans-serif;color:var(--ink);font-size:12px;line-height:1.6}
.abs{position:absolute}
.photo{position:absolute}
.btn{position:absolute;display:flex;align-items:center;justify-content:center;gap:8px;height:34px;border-radius:17px;color:var(--white);font-weight:600;font-size:10px;letter-spacing:1px;text-transform:uppercase}
.btn-teal{background:var(--teal)}
.btn-green{background:var(--green)}
.btn .dot{width:12px;height:12px;border-radius:50%;border:2px solid var(--white)}
.brand{font-family:'Josefin Sans',sans-serif;font-weight:700;color:var(--green);font-size:26px;letter-spacing:1px;display:flex;align-items:center;gap:10px;text-transform:uppercase}
.brand .mark{width:14px;height:14px;border-radius:50%;background:var(--green)}

/* header */
.nav{position:absolute;top:42px;left:450px;display:flex;gap:34px;font-size:10px;font-weight:600;letter-spacing:1px;text-transform:uppercase}
.nav a{color:var(--ink);text-decoration:none}
.nav a.active{color:var(--teal);border-bottom:2px solid var(--teal);padding-bottom:4px}
.hero-title{position:absolute;top:128px;left:0;width:1200px;text-align:center;font-family:'Josefin Sans',sans-serif;font-weight:700;font-size:54px;line-height:1.1;color:var(--green);text-transform:uppercase}
.hero-sub{position:absolute;top:232px;left:420px;width:360px;text-align:center;font-size:12px;color:var(--ink)}

/* about */
.section-title{position:absolute;left:0;width:1200px;text-align:center;font-family:'Josefin Sans',sans-serif;font-weight:700;font-size:40px;text-transform:uppercase}
.section-title span{display:block;width:70px;height:3px;margin:10px auto 0;background:currentColor}
.col-title{position:absolute;font-family:'Playfair Display',serif;font-size:22px;color:var(--white)}
.service-box{position:absolute;left:112px;top:826px;width:270px;height:306px;background:var(--green-light);border-radius:6px;padding:26px 24px;color:var(--white)}
.service-item{display:flex;gap:14px;margin-bottom:30px}
.service-item .ic{width:30px;height:30px;border-radius:50%;background:rgba(255,255,255,.25);flex:none}
.service-item small{display:block;font-size:10px;opacity:.85}
.service-item b{font-size:15px;font-weight:600}
.about-text{position:absolute;color:var(--white);font-size:11px}

/* pastor */
.pastor-card{position:absolute;left:208px;top:1360px;width:880px;height:460px;border:1px solid var(--line);border-radius:8px;box-shadow:0 10px 30px rgba(0,0,0,.05)}
.badge{position:absolute;left:160px;top:1440px;width:110px;height:110px;border-radius:50%;background:var(--teal);border:6px solid #bfeaf4;color:var(--white);text-align:center;padding-top:22px;font-family:'Josefin Sans',sans-serif}
.badge b{display:block;font-size:30px;line-height:1}
.badge small{font-size:10px;letter-spacing:1px;text-transform:uppercase}
.name-pill{position:absolute;left:400px;top:1668px;width:180px;height:40px;border-radius:20px;background:var(--white);box-shadow:0 6px 18px rgba(0,0,0,.15);display:flex;align-items:center;justify-content:center;font-size:10px;font-weight:600;letter-spacing:1px;color:var(--green-dark)}
.pastor-heading{position:absolute;left:650px;top:1480px;font-family:'Josefin Sans',sans-serif;font-weight:700;font-size:42px;color:var(--green);text-transform:uppercase}
.pastor-text{position:absolute;left:650px;width:380px;font-size:11px;color:var(--muted)}
.verse{position:absolute;left:650px;top:1714px;width:380px;border-left:3px solid var(--teal);padding-left:12px;font-size:11px;font-style:italic;color:var(--green-dark)}

/* beliefs */
.beliefs{position:absolute;left:0;top:1880px;width:1200px;height:1600px;background:var(--sky)}
.belief{position:absolute;background:var(--white);border-radius:10px;box-shadow:0 8px 24px rgba(30,90,120,.08);padding:28px 30px}
.belief .ic{width:40px;height:40px;border-radius:8px;background:var(--green);margin-bottom:14px}
.belief h3{font-family:'Playfair Display',serif;font-weight:700;font-size:24px;color:var(--ink);display:flex;align-items:center;gap:14px;margin-bottom:14px}
.belief h3::after{content:"";flex:1;height:1px;background:var(--green)}
.belief p{font-size:10.5px;color:var(--muted);margin-bottom:12px}
.ref{display:inline-flex;align-items:center;gap:10px;background:#eef7f0;border-radius:4px;padding:6px 12px 6px 6px;font-size:10px;font-weight:500;margin:0 6px 8px 0}
.ref::before{content:"";width:20px;height:20px;border-radius:4px;background:var(--teal)}
.belief.featured{background:var(--teal);color:var(--white)}
.belief.featured h3,.belief.featured p{color:var(--white)}
.belief.featured h3::after{background:var(--white)}
.belief.featured .ic{background:var(--white)}
.belief.featured .strong{font-weight:600;font-size:11px;text-transform:uppercase}
.hl{background:var(--green);padding:1px 6px;border-radius:3px}

/* support */
.help-title{position:absolute;left:150px;top:3614px;width:540px;font-family:'Josefin Sans',sans-serif;font-weight:700;font-size:40px;color:var(--green);text-transform:uppercase;line-height:1;white-space:nowrap}
.help-sub{position:absolute;left:150px;top:3666px;width:540px;font-family:'Josefin Sans',sans-serif;font-weight:600;font-size:23px;color:var(--ink);text-transform:uppercase;line-height:1.2}

/* contact */
.field{position:absolute;height:42px;border-radius:21px;background:var(--white);padding:0 22px;display:flex;align-items:center;font-size:11px;color:#9a9a9a}
.field.msg{height:130px;border-radius:16px;align-items:flex-start;padding-top:14px}

/* footer */
.foot-col{position:absolute;top:4800px;font-size:11px;color:var(--ink)}
.foot-col h4{font-size:11px;font-weight:600;letter-spacing:1px;text-transform:uppercase;margin-bottom:12px}
.foot-col p{color:var(--muted);line-height:1.9}
.copy{position:absolute;top:5010px;left:0;width:1200px;text-align:center;font-size:10px;color:var(--muted)}
</style>
</head>
<body>

<!-- Header -->
<div class="photo" role="img" aria-label="Brick church building with white steeple under a cloudy sky" style="left:0;top:90px;width:1200px;height:570px;background:linear-gradient(180deg,#ffffff 0%,#f3f3f1 30%,#c9b8a8 55%,#9a6f55 72%,#6f8f5a 100%)"></div>
<div class="abs" style="left:0;top:0;width:1200px;height:340px;background:linear-gradient(180deg,#fff 55%,rgba(255,255,255,0) 100%)"></div>
<div class="brand abs" style="left:90px;top:30px"><span class="mark"></span>Cedar Hill</div>
<nav class="nav"><a class="active">Home</a><a>Support Us</a><a>Recording Library</a></nav>
<div class="btn btn-teal" style="left:990px;top:34px;width:100px;height:28px"><span class="dot"></span>Login</div>
<h1 class="hero-title">God Give Us Power<br>To Believe Trinity</h1>
<p class="hero-sub">We believe in the God head bodily, known as the Divine Trinity. We are a conservative, evangelical, Christian church.</p>
<div class="btn btn-teal" style="left:470px;top:282px;width:120px"><span class="dot"></span>Listen Live</div>
<div class="btn btn-green" style="left:610px;top:282px;width:120px"><span class="dot"></span>Donate</div>

<!-- About -->
<svg class="abs" style="left:0;top:555px" width="1200" height="610" viewBox="0 0 1200 610">
  <polygon points="0,90 560,40 600,0 640,40 1200,90 1200,610 0,610" fill="#4b7b2f"/>
</svg>
<h2 class="section-title" style="top:690px;color:var(--white)">About Us<span></span></h2>

<div class="col-title" style="left:112px;top:780px">Service Times.</div>
<div class="service-box">
  <div class="service-item"><span class="ic"></span><div><small>Wednesday Evening Service</small><b>7:30 PM Sunday School, 10:00 AM</b></div></div>
  <div class="service-item"><span class="ic"></span><div><small>Sunday Morning Service</small><b>11:00 AM Sunday</b></div></div>
  <div class="service-item"><span class="ic"></span><div><small>Evening Service</small><b>6:00 PM</b></div></div>
</div>

<div class="col-title" style="left:410px;top:780px">Location</div>
<div class="about-text" style="left:410px;top:830px;font-weight:600;letter-spacing:1px">CEDAR HILL HOLINESS CHURCH</div>
<svg class="abs" style="left:410px;top:860px" width="18" height="24" viewBox="0 0 18 24"><path d="M9 0C4 0 0 4 0 9c0 7 9 15 9 15s9-8 9-15c0-5-4-9-9-9z" fill="#1bb4d5"/><circle cx="9" cy="9" r="3.5" fill="#4b7b2f"/></svg>
<div class="about-text" style="left:438px;top:858px;font-size:13px">4120 Meadow Rd, Brookline,<br>TN 37010</div>
<div class="photo" role="img" aria-label="Street map showing the church location" style="left:410px;top:932px;width:280px;height:200px;border-radius:6px;background:linear-gradient(135deg,#eef0ea,#dfe6dc 50%,#e9e4d8)"></div>

<div class="col-title" style="left:745px;top:780px">About Church.</div>
<p class="about-text" style="left:745px;top:828px;width:345px">Lorem ipsum dolor sit amet consectetur adipiscing elit, sed do eiusmod tempor incididunt ut labore et dolore magna aliqua, ut enim ad minim veniam quis nostrud exercitation ullamco laboris nisi ut aliquip.</p>
<div class="photo" role="img" aria-label="Brick church building exterior" style="left:745px;top:932px;width:345px;height:200px;border-radius:6px;background:linear-gradient(160deg,#c8c9c6 0%,#a8745a 55%,#6e8a52 100%)"></div>

<!-- Pastor -->
<div class="pastor-card"></div>
<div class="photo" role="img" aria-label="Portrait of the pastor standing at a pulpit" style="left:208px;top:1300px;width:392px;height:520px;border-radius:196px 196px 0 8px;background:linear-gradient(180deg,#e8e6e2 0%,#b9b3ab 55%,#6d5a4c 100%)"></div>
<div class="badge"><b>25</b><small>Years</small></div>
<div class="name-pill">PASTOR DANIEL REED</div>
<h2 class="pastor-heading">Our Pastor</h2>
<p class="pastor-text" style="top:1540px">Lorem ipsum dolor sit amet consectetur adipiscing elit sed do eiusmod tempor incididunt ut labore et dolore magna aliqua. Ut enim ad minim veniam, quis nostrud exercitation ullamco laboris nisi ut aliquip ex ea commodo consequat duis aute irure.</p>
<p class="pastor-text" style="top:1636px">Lorem ipsum dolor sit amet consectetur adipiscing elit sed do eiusmod tempor incididunt ut labore et dolore magna aliqua ut enim minim veniam.</p>
<p class="verse">“And I will give you pastors according to mine heart, which shall feed you with knowledge and understanding.” Jer 3:15 LPW</p>

<!-- Beliefs -->
<div class="beliefs"></div>
<h2 class="section-title" style="top:2000px;color:var(--green)">What We Believe<span></span></h2>

<div class="belief" style="left:228px;top:2090px;width:364px;height:270px">
  <div class="ic"></div><h3>The God Head.</h3>
  <p>We believe in the God head bodily, known as the Divine Trinity. The body consists of God the Father, Jesus Christ, His only begotten Son, and the Holy Ghost, all of one mind and purpose.</p>
</div>
<div class="belief featured" style="left:608px;top:2060px;width:372px;height:320px">
  <div class="ic"></div><h3>Sanctification.</h3>
  <p>Sanctification is a second, definite work of grace through faith, <span class="hl">Hebrews 13:12</span> cleansing the heart of believers from inbred sin.</p>
  <p class="strong">We believe in a set apart life, separate from the world to Christ (Cor 6:17)</p>
</div>
<div class="belief" style="left:228px;top:2400px;width:364px;height:480px">
  <div class="ic"></div><h3>Baptism of the Holy Ghost.</h3>
  <p>We believe in the baptism of the Holy Ghost as it is taught in the Word and promised by our Lord Jesus Christ, with speaking in tongues as the Spirit gives utterance.</p>
  <span class="ref">Acts 2:4</span><span class="ref">Acts 2:17-18</span>
  <p>We believe that the gift of the Holy Ghost is for all believers, as the Lord promised to those who ask.</p>
  <span class="ref">Acts 2:39</span>
</div>
<div class="belief" style="left:608px;top:2420px;width:372px;height:340px">
  <div class="ic"></div><h3>Divine Healing.</h3>
  <p>We believe divine healing is provided in the atonement of Jesus Christ, our Lord, and is available to all who believe and pray in faith.</p>
  <span class="ref">1 Peter 2:24 Isa 53:4-5</span><br><span class="ref">Mark 16:18 James 5:14</span>
</div>
<div class="belief" style="left:228px;top:2920px;width:364px;height:260px">
  <div class="ic"></div><h3>Second Coming of Christ</h3>
  <p>We believe in the second coming of Jesus Christ to gather His church unto Himself.</p>
  <span class="ref">Matthew 24:44 Luke 12:40</span>
</div>
<div class="belief" style="left:608px;top:2800px;width:372px;height:640px">
  <div class="ic"></div><h3>Full Salvation.</h3>
  <p>We believe that Salvation is received only when a person comes to the realization that he or she is lost, and repentant from sin and transgression, believing in the shed blood of the Lord Jesus Christ as the only sacrifice for sin, through the Word of God and grace.</p>
  <span class="ref">Romans 10:9-10 Matthew 26:28</span><br>
  <span class="ref">Sanctification, Hebrews 13:12</span><br>
  <span class="ref">Redemption, Ephesians 1:7</span><br>
  <span class="ref">Atonement, 1 John 1:7 Rom 5:11</span><br>
  <span class="ref">Justification, Romans 5:9</span>
</div>
<div class="belief" style="left:228px;top:3220px;width:364px;height:220px">
  <div class="ic"></div><h3>Eternity</h3>
  <p>We believe in eternal life for the believer, and eternal punishment for those without Christ.</p>
  <span class="ref">Revelation 21:1-27</span>
</div>

<!-- Support -->
<div class="abs" style="left:770px;top:3560px;width:350px;height:350px;border-radius:50%;background:var(--teal)"></div>
<div class="photo" role="img" aria-label="Pastor preaching at a wooden pulpit" style="left:730px;top:3520px;width:390px;height:520px;border-radius:195px 195px 0 0;background:linear-gradient(180deg,rgba(230,230,228,.9) 0%,rgba(180,178,175,.9) 50%,rgba(110,85,65,.95) 100%)"></div>
<h2 class="help-title">Bring Help &amp; Hope</h2>
<p class="help-sub">To the people who depend and<br>believe in the God head</p>
<div class="btn btn-teal" style="left:150px;top:3744px;width:130px"><span class="dot"></span>Support Us</div>
<div class="btn btn-green" style="left:296px;top:3744px;width:120px"><span class="dot"></span>Donate</div>

<!-- Contact -->
<div class="photo" role="img" aria-label="Church building behind a green overlay" style="left:0;top:4040px;width:1200px;height:700px;background:linear-gradient(180deg,#4b7b2f 0%,#557f38 50%,#3c6625 100%)"></div>
<svg class="abs" style="left:0;top:4680px" width="1200" height="70" viewBox="0 0 1200 70"><path d="M0 0 H1200 V20 Q600 90 0 20 Z" fill="#3c6625"/><path d="M0 20 Q600 90 1200 20 V70 H0 Z" fill="#fff"/></svg>
<h2 class="section-title" style="top:4240px;color:var(--white)">Contact Us<span></span></h2>
<div class="field" style="left:210px;top:4348px;width:380px">First Name</div>
<div class="field" style="left:610px;top:4348px;width:380px">Last Name</div>
<div class="field" style="left:210px;top:4408px;width:380px">Email Address</div>
<div class="field" style="left:610px;top:4408px;width:380px">Phone Number</div>
<div class="field msg" style="left:210px;top:4468px;width:780px">Message</div>
<div class="btn btn-teal" style="left:530px;top:4640px;width:140px">Submit Now</div>

<!-- Footer -->
<div class="foot-col" style="left:110px"><h4>Links</h4><p>Home<br>Support Us<br>Recording Library<br>Login</p></div>
<div class="foot-col" style="left:290px"><h4>Location</h4><p>4120 Meadow Rd,<br>Brookline, TN 37010</p></div>
<div class="brand abs" style="left:500px;top:4880px"><span class="mark"></span>Cedar Hill</div>
<div class="foot-col" style="left:745px"><h4>Location</h4><p>4120 Meadow Rd,<br>Brookline, TN 37010</p></div>
<div class="btn btn-teal" style="left:940px;top:4800px;width:130px"><span class="dot"></span>Listen Live</div>
<div class="btn btn-green" style="left:940px;top:4846px;width:130px"><span class="dot"></span>Donate</div>
<p class="copy">© 2024 Cedar Hill Holiness Church. All rights reserved.</p>
<div class="photo" role="img" aria-label="Brick church building exterior" style="left:0;top:5060px;width:1200px;height:164px;background:linear-gradient(180deg,#ffffff 0%,#d8cfc6 35%,#a2735a 70%,#6b8a50 100%)"></div>

</body>
</html>
```